Wordpress Powered Website. Outstanding Design Required. Using Morvenic Theme

Designers will not need to create anything other than the home page but there are some design elements on the home page which also need to be factored in: 6 product place holders and 2-3 slides for a slideshow (with images I provide).

Designers will need to familiarise themselves with the Morvenic theme to make sure that their design will work within the theme.

The winning designer will set up all the pages and navigation in place. This includes social media icons, favicon, widgets, etc. In other words, the home page needs to be designed and coded and the other preset theme pages need to be organised in a way that we can start using the website on completion of the job.

Most of the designs I had last time were too colourful. This needs to be subtle not in your face.

Background to the business/website:
Ridgeway Banners is a new Australian venture which will sell large format printed banners and other signage. The market is very competitive so it is important to stand out visually and to have a website which is clean, easy to navigate and easy to order. It will be a combination of online sales and assisted sales but all sales enquiries will come from the website.

As our business is focused on presentation it is vital to have excellent design.
Purchased theme is Morvenic. Only this theme is to be used.

1. A home page using all the preset features of the Morvenic theme - it will just be basically taking my wireframe and inputting it to the live theme.
2. A three slide slideshow, ideally with an edited video. The static image slides can be provided by me during the handover. Placeholder for now.
Similar to this one: http://thecedarhollow.example.au/

Attached is the logo which must be utilised, although it could also sit on a dark background. There is our mascot as well which can be used but does not have to be included.

Target Market(s)

Primarily B2B (business to business)
Main industries will be Construction, Retail, Community, Events & Trade Shows

Industry/Entity Type

Printing

Coding

Coded - Design and coding required

Font styles to use
Sans Serif

Requirements
Must have
• Must have the design files made to web pages within the Wordpress environment.
Nice to have
• Clean design. Stand out from competitors based on design.
Should not have
• Should not look like any competitor

```html
<!DOCTYPE html>
<html lang="en">
<head>
<meta charset="utf-8">
<title>Ridgeway Banners – Large Format Printed Banners</title>
<link href="https://fonts.googleapis.com/css2?family=Open+Sans:ital,wght@0,400;0,600;0,700;1,400;1,600;1,700&display=swap" rel="stylesheet">
<style>
:root{
  --blue:#1773c9;
  --blue-dark:#0f5fae;
  --ink:#222;
  --text:#444;
  --muted:#666;
  --light:#f3f3f3;
  --line:#dcdcdc;
  --black:#111;
  --green:#5a9a26;
  --green-light:#7cbb3a;
  --white:#fff;
}
*{box-sizing:border-box;margin:0;padding:0}
html,body{width:1200px;height:2711px;overflow:hidden}
body{font-family:"Open Sans",Arial,sans-serif;color:var(--text);background:var(--white);position:relative}
.section{position:absolute;left:0;width:1200px}
.btn-outline{display:inline-block;border:2px solid var(--blue);color:var(--blue);font-size:12px;font-weight:700;letter-spacing:.3px;text-align:center;background:var(--white)}

/* top bar */
.topbar{top:0;height:36px;background:var(--black);color:var(--white)}
.social{position:absolute;left:100px;top:11px;display:flex;gap:13px}
.social span{width:13px;height:13px;border-radius:50%;background:#e8e8e8;display:block}
.contact-line{position:absolute;right:100px;top:8px;display:flex;gap:26px;font-size:14px;font-weight:600}
.contact-line div{display:flex;align-items:center;gap:8px}

/* header */
.header{top:36px;height:84px;background:var(--white);border-bottom:1px solid #e5e5e5}
.brand{position:absolute;left:99px;top:22px;display:flex;align-items:center;gap:10px}
.brand-mark{width:40px;height:40px;background:var(--blue);border-radius:50%}
.brand-name{font-size:26px;font-weight:700;color:var(--blue);letter-spacing:-.3px}
.nav{position:absolute;left:505px;top:24px;display:flex;align-items:center;font-size:13px;font-weight:600;color:var(--ink)}
.nav a{color:inherit;text-decoration:none;padding:0 25px;border-left:1px solid #ddd;line-height:14px}
.nav a:first-child{border:none}
.nav .active{background:var(--blue);color:var(--white);padding:10px 18px;margin-right:0}

/* hero */
.hero{top:120px;height:428px;background:
  radial-gradient(ellipse at 25% 30%,rgba(214,156,90,.75),transparent 55%),
  radial-gradient(ellipse at 80% 70%,rgba(90,110,150,.7),transparent 55%),
  radial-gradient(ellipse at 55% 45%,rgba(190,90,110,.55),transparent 50%),
  linear-gradient(120deg,#7a6f6a,#9c8f88 40%,#6f7688)}
.hero-copy{position:absolute;top:152px;width:100%;text-align:center;color:var(--white);font-size:28px;font-weight:700;line-height:41px;text-shadow:0 2px 6px rgba(0,0,0,.45)}
.hero-btn{position:absolute;left:525px;top:254px;width:152px;height:33px;border:2px solid var(--white);color:var(--white);font-size:13px;font-weight:600;text-align:center;line-height:29px;background:rgba(0,0,0,.25)}
.dots{position:absolute;top:396px;left:0;width:100%;display:flex;justify-content:center;gap:9px}
.dots span{width:13px;height:13px;border:2px solid var(--white);border-radius:50%}
.dots .on{background:var(--blue)}

/* section headings */
.heading{text-align:center;font-size:24px;font-weight:600;color:var(--ink);letter-spacing:.3px}
.heading-rule{width:480px;height:1px;background:var(--line);margin:12px auto 0}

/* about */
.about{top:548px;height:256px}
.about .heading{margin-top:30px}
.about p{width:990px;margin:32px auto 0;text-align:center;font-size:12.5px;line-height:23px;color:var(--muted)}
.about .btn-outline{position:absolute;left:540px;top:191px;width:120px;height:31px;line-height:27px}

/* features */
.features{top:804px;height:407px;background:var(--light);display:flex;justify-content:center;gap:0;padding-left:0}
.feature{width:257px;text-align:center;padding-top:51px}
.feature-icon{width:112px;height:112px;border-radius:50%;background:var(--blue);margin:0 auto;display:flex;align-items:center;justify-content:center}
.feature h3{font-size:16px;font-weight:600;color:var(--ink);margin-top:25px}
.feature p{font-size:12.5px;line-height:23px;color:var(--muted);margin:22px auto 0;width:210px}
.feature .btn-outline{width:122px;height:31px;line-height:27px;margin-top:20px}

/* products */
.products{top:1211px;height:564px;background:linear-gradient(135deg,#5b5c60,#3c3d42 50%,#55545a)}
.products::before{content:"";position:absolute;inset:0;background:rgba(20,20,25,.35)}
.products .heading{position:relative;color:var(--white);margin-top:50px}
.product-grid{position:absolute;left:98px;top:135px;display:flex;gap:14px}
.product{width:240px;height:362px;display:flex;flex-direction:column}
.product .photo{height:181px}
.product .info{height:181px;text-align:center;padding-top:15px}
.info.white{background:var(--white)}
.info.blue{background:var(--blue);color:var(--white)}
.info h4{font-size:16.5px;font-weight:600;color:var(--ink)}
.info.blue h4{color:var(--white)}
.info p{font-size:12px;line-height:19px;color:var(--muted);margin:10px auto 0;width:220px}
.info.blue p{color:#e6f0fb}
.info .btn-outline{width:122px;height:31px;line-height:27px;margin-top:12px}
.info.blue .btn-outline{background:var(--blue);border-color:var(--white);color:var(--white)}

/* why */
.why{top:1775px;height:357px;background:var(--light)}
.why-text{position:absolute;left:100px;top:40px;width:460px}
.why-text h2{font-size:24px;font-weight:600;color:var(--ink)}
.why-text p{font-size:12.5px;line-height:23px;color:var(--muted);margin-top:24px}
.perks{position:absolute;left:100px;top:206px;display:grid;grid-template-columns:260px 260px;row-gap:20px}
.perk{display:flex;align-items:center;gap:12px;font-size:12.5px;font-weight:600;color:var(--ink)}
.perk .dot{width:43px;height:43px;border-radius:50%;background:var(--blue);display:flex;align-items:center;justify-content:center}
.why-photo{position:absolute;left:600px;top:3px;width:600px;height:354px;background:linear-gradient(100deg,#d9dade,#c5c7cc 45%,#8a8f9c 70%,#c9ccd1)}

/* testimonials */
.testimonials{top:2132px;height:347px}
.testimonials .heading{margin-top:38px}
.quote{width:800px;margin:32px auto 0;text-align:center;font-style:italic;font-size:12.5px;line-height:23px;color:var(--muted)}
.arrow{position:absolute;top:133px}
.arrow.left{left:99px}
.arrow.right{right:99px}
.client{position:absolute;left:479px;top:217px;display:flex;align-items:center}
.quote-badge{width:62px;height:62px;border-radius:50%;background:var(--blue);display:flex;align-items:center;justify-content:center;color:var(--white);font-size:44px;font-weight:700;line-height:1;padding-top:18px;position:relative;z-index:1}
.avatar{width:80px;height:80px;border-radius:50%;border:4px solid var(--white);background:linear-gradient(160deg,#c9a98d,#8d6e58);box-shadow:0 0 0 1px #ddd;margin-left:-12px}
.client-name{margin-left:14px}
.client-name strong{display:block;color:var(--blue);font-size:17px;font-weight:600}
.client-name span{font-size:12.5px;color:var(--muted)}

/* help band */
.help{top:2479px;height:163px;background:linear-gradient(90deg,var(--green),var(--green-light) 60%,var(--green))}
.help h2{text-align:center;color:var(--white);font-style:italic;font-weight:700;font-size:24px;margin-top:33px}
.help-items{position:absolute;top:94px;left:99px;width:1010px;display:flex;justify-content:space-between}
.help-item{display:flex;align-items:center;gap:14px;color:var(--white)}
.help-item strong{display:block;font-style:italic;font-weight:600;font-size:18px;line-height:22px}
.help-item span{font-size:12.5px;color:#e3f0d4}

/* footer */
.footer{top:2642px;height:69px;background:#1b1b1b;color:var(--white);font-size:12.5px;font-weight:700}
.footer-links{position:absolute;left:99px;top:26px}
.footer-social{position:absolute;left:622px;top:28px;display:flex;gap:14px}
.footer-social span{width:12px;height:12px;border-radius:50%;background:#ddd;display:block}
.copyright{position:absolute;right:100px;top:27px;font-size:11px}
</style>
</head>
<body>

<div class="section topbar">
  <div class="social"><span></span><span></span><span></span><span></span><span></span></div>
  <div class="contact-line">
    <div><svg width="16" height="11" viewBox="0 0 16 11"><rect x="0.5" y="0.5" width="15" height="10" fill="#fff"/><path d="M1 1l7 5 7-5" fill="none" stroke="#111" stroke-width="1.3"/></svg>info@ridgewaybanners.example</div>
    <div><svg width="13" height="13" viewBox="0 0 24 24"><path fill="#fff" d="M6.6 10.8a15.1 15.1 0 006.6 6.6l2.2-2.2c.3-.3.7-.4 1-.2 1.1.4 2.3.6 3.6.6.6 0 1 .4 1 1V20c0 .6-.4 1-1 1A17 17 0 013 4c0-.6.4-1 1-1h3.5c.6 0 1 .4 1 1 0 1.3.2 2.5.6 3.6.1.3 0 .7-.2 1z"/></svg>123-456-7890</div>
  </div>
</div>

<header class="section header">
  <div class="brand"><span class="brand-mark"></span><span class="brand-name">Ridgeway Banners</span></div>
  <nav class="nav">
    <a class="active">Home</a><a>About Us</a><a>Product</a><a>Category</a><a>FAQ's</a><a>Contact Us</a>
  </nav>
</header>

<section class="section hero" role="img" aria-label="Slideshow photo of fanned printed sheets in many colours">
  <div class="hero-copy">We Are A New Australian Firm Which Will Sell<br>Large Format Printed Banners And Other Signage Material</div>
  <div class="hero-btn">CONACT NOW !</div>
  <div class="dots"><span></span><span class="on"></span><span></span><span></span></div>
</section>

<section class="section about">
  <h2 class="heading">ABOUT RIDGEWAY BANNERS</h2>
  <div class="heading-rule"></div>
  <p>Lorem ipsum dolor sit amet, consectetur adipiscing elit. Aenean et dignissim sem, interdum risus. Vestibulum consectetur nisi mollis diam pulvinar adipiscing. Vestibulum ut urna nec nibh adipiscing facilisis. Etiam auctor porta lacus ac luctus. Praesent ac libero fermentum, rhoncus magna a, dapibus mauris. Nam ut auctor justo. Sed ante odio, luctus quis nequ nec, adipiscing eleifend arcu. Integer nunc turpis, porttitor at lorem ut.Quisque hendrerit</p>
  <span class="btn-outline">READ MORE</span>
</section>

<section class="section features">
  <div class="feature">
    <div class="feature-icon"><svg width="46" height="46" viewBox="0 0 24 24"><path fill="#fff" d="M2 10h4v11H2zM8 21h9.5c.8 0 1.5-.5 1.8-1.2l2.5-6.3c.1-.3.2-.6.2-.9V11c0-1.1-.9-2-2-2h-6l1-4.6c.1-.6-.1-1.1-.5-1.5L14 2 8 8.5z"/></svg></div>
    <h3>Quality Printing</h3>
    <p>Lorem ipsum dolor sit amet, consectetur adipiscing elit. Aenean et dignissim sem, interdum risus.</p>
    <span class="btn-outline">READ MORE</span>
  </div>
  <div class="feature">
    <div class="feature-icon"><svg width="48" height="48" viewBox="0 0 24 24" fill="none" stroke="#fff" stroke-width="2"><circle cx="13" cy="13" r="8"/><path d="M13 9v4l3 2M11 2h4M2 11h4M3 15h3"/></svg></div>
    <h3>Timely Delivery</h3>
    <p>Lorem ipsum dolor sit amet, consectetur adipiscing elit. Aenean et dignissim sem, interdum risus.</p>
    <span class="btn-outline">READ MORE</span>
  </div>
  <div class="feature">
    <div class="feature-icon"><svg width="48" height="48" viewBox="0 0 24 24"><circle cx="12" cy="12" r="9" fill="none" stroke="#fff" stroke-width="2"/><path fill="#fff" d="M8 16c0-5 3-8 9-9-1 6-4 9-9 9z"/></svg></div>
    <h3>Eco-Minded</h3>
    <p>Lorem ipsum dolor sit amet, consectetur adipiscing elit. Aenean et dignissim sem, interdum risus.</p>
    <span class="btn-outline">READ MORE</span>
  </div>
  <div class="feature">
    <div class="feature-icon"><svg width="46" height="46" viewBox="0 0 24 24"><rect x="5" y="3" width="14" height="18" rx="2" fill="#fff"/><text x="12" y="16" text-anchor="middle" font-size="11" font-weight="700" fill="#1773c9" font-family="Open Sans,sans-serif">$</text></svg></div>
    <h3>Money Back Guaranteed</h3>
    <p>Lorem ipsum dolor sit amet, consectetur adipiscing elit. Aenean et dignissim sem, interdum risus.</p>
    <span class="btn-outline">READ MORE</span>
  </div>
</section>

<section class="section products">
  <h2 class="heading">PRODUCT CATEGORIES</h2>
  <div class="product-grid">
    <div class="product">
      <div class="photo" role="img" aria-label="Photo of a large format printer in a print shop" style="background:linear-gradient(160deg,#d6d6d6,#9a9c9f)"></div>
      <div class="info white"><h4>Lorem ipsum dolor sit</h4><p>Lorem ipsum dolor sit amet, consectetur adipiscing elit. Aenean et dignissim sem, interdum risus.</p><span class="btn-outline">READ MORE</span></div>
    </div>
    <div class="product">
      <div class="info blue"><h4>Lorem ipsum dolor sit</h4><p>Lorem ipsum dolor sit amet, consectetur adipiscing elit. Aenean et dignissim sem, interdum risus.</p><span class="btn-outline">READ MORE</span></div>
      <div class="photo" role="img" aria-label="Photo of a colourful banner coming out of a printer" style="background:linear-gradient(160deg,#6a6c72,#b8a3b5 50%,#5b7fa8)"></div>
    </div>
    <div class="product">
      <div class="photo" role="img" aria-label="Photo of illuminated advertising panels in a shopping centre" style="background:linear-gradient(160deg,#c7ccd3,#8fa5c4 50%,#d9b98f)"></div>
      <div class="info white"><h4>Lorem ipsum dolor sit</h4><p>Lorem ipsum dolor sit amet, consectetur adipiscing elit. Aenean et dignissim sem, interdum risus.</p><span class="btn-outline">READ MORE</span></div>
    </div>
    <div class="product">
      <div class="info blue"><h4>Lorem ipsum dolor sit</h4><p>Lorem ipsum dolor sit amet, consectetur adipiscing elit. Aenean et dignissim sem, interdum risus.</p><span class="btn-outline">READ MORE</span></div>
      <div class="photo" role="img" aria-label="Photo of printing press rollers with colourful prints" style="background:linear-gradient(160deg,#5b6e86,#4e9ac6 50%,#8dbb63)"></div>
    </div>
  </div>
</section>

<section class="section why">
  <div class="why-text">
    <h2>WHY CHOOSE RIDGEWAY BANNERS</h2>
    <p>Lorem ipsum dolor sit amet, consectetur adipiscing elit. Aenean et dignissim sem, interdum risus. Vestibulum consectetur nisi mollis diam pulvinar adipisc Vestibulum ut urna nec nibh adipiscing facilisis Lorem ipsum dolor sit amet, consectetur adipiscing elit.</p>
  </div>
  <div class="perks">
    <div class="perk"><span class="dot"><svg width="20" height="20" viewBox="0 0 24 24"><circle cx="12" cy="9" r="6" fill="none" stroke="#fff" stroke-width="2"/><path d="M8 14l-2 8 6-3 6 3-2-8" fill="#fff"/></svg></span>100% Quality Guarantee</div>
    <div class="perk"><span class="dot"><svg width="22" height="22" viewBox="0 0 24 24"><circle cx="12" cy="12" r="9" fill="none" stroke="#fff" stroke-width="2"/><text x="12" y="16.5" text-anchor="middle" font-size="12" font-weight="700" fill="#fff" font-family="Open Sans,sans-serif">$</text></svg></span>Best Price Guarantee</div>
    <div class="perk"><span class="dot"><svg width="24" height="20" viewBox="0 0 24 20"><rect x="1" y="4" width="14" height="10" fill="#fff"/><path d="M15 7h4l3 4v3h-7z" fill="#fff"/><circle cx="6" cy="16" r="2" fill="#fff"/><circle cx="18" cy="16" r="2" fill="#fff"/></svg></span>Free Shipping</div>
    <div class="perk"><span class="dot"><svg width="22" height="22" viewBox="0 0 24 24" fill="none" stroke="#fff" stroke-width="2"><rect x="3" y="5" width="18" height="13"/><path d="M8 14l8-6M13 8h3v3"/></svg></span>Free Design Proofs</div>
  </div>
  <div class="why-photo" role="img" aria-label="Photo of a man operating a large office printer"></div>
</section>

<section class="section testimonials">
  <h2 class="heading">WHAT OUR CLIENTS SAY</h2>
  <div class="heading-rule"></div>
  <p class="quote">Lorem ipsum dolor sit amet, consectetuer adipiscing elit, sed diam nonummy nibh euismod tincidunt ut laoreet dolore magna aliquam erat volutpat. Ut wisi enim minim veniam, quis nostrud exerci tation ullamcorper suscipit lobortis nisl ut aliquip ex ea commodo consequat. Ut wisi enim minim veniam, quis nostrud exerci tation ullamcorper suscipit lobortis nisl ut aliquip ex ea commodo consequat.</p>
  <svg class="arrow left" width="30" height="58" viewBox="0 0 30 58"><path d="M28 2L2 29l26 27" fill="none" stroke="#666" stroke-width="2"/></svg>
  <svg class="arrow right" width="30" height="58" viewBox="0 0 30 58"><path d="M2 2l26 27L2 56" fill="none" stroke="#666" stroke-width="2"/></svg>
  <div class="client">
    <div class="quote-badge">&ldquo;</div>
    <div class="avatar" role="img" aria-label="Client portrait photo"></div>
    <div class="client-name"><strong>Aaron Whitfield</strong><span>Lorem Ipsum</span></div>
  </div>
</section>

<section class="section help">
  <h2>We're Dedicated to Our Customers 24x7</h2>
  <div class="help-items">
    <div class="help-item"><svg width="40" height="40" viewBox="0 0 24 24"><path fill="#fff" d="M6.6 10.8a15.1 15.1 0 006.6 6.6l2.2-2.2c.3-.3.7-.4 1-.2 1.1.4 2.3.6 3.6.6.6 0 1 .4 1 1V20c0 .6-.4 1-1 1A17 17 0 013 4c0-.6.4-1 1-1h3.5c.6 0 1 .4 1 1 0 1.3.2 2.5.6 3.6.1.3 0 .7-.2 1z"/></svg><div><strong>123-456-7890</strong><span>Available 24/7 - Call us any time.</span></div></div>
    <div class="help-item"><svg width="44" height="32" viewBox="0 0 44 32" fill="none" stroke="#fff" stroke-width="2.5"><rect x="2" y="2" width="40" height="28"/><path d="M2 2l20 16L42 2M2 30l14-14M42 30L28 16"/></svg><div><strong>Email Us</strong><span>Have a question? Let us help.</span></div></div>
    <div class="help-item"><svg width="44" height="36" viewBox="0 0 44 36" fill="none" stroke="#fff" stroke-width="2.5"><ellipse cx="18" cy="14" rx="16" ry="11"/><path d="M8 23l-3 8 9-5"/><path d="M36 12c4 2 6 5 6 8 0 3-2 6-5 7l2 6-7-4"/></svg><div><strong>Live Chat</strong><span>Online Support</span></div></div>
    <div class="help-item"><svg width="26" height="40" viewBox="0 0 26 40"><text x="13" y="34" text-anchor="middle" font-size="40" font-weight="700" fill="#fff" font-family="Open Sans,sans-serif">?</text></svg><div><strong>Help</strong><span>Find your answers.</span></div></div>
  </div>
</section>

<footer class="section footer">
  <div class="footer-links">Home &nbsp;/&nbsp; About Us &nbsp;/&nbsp; Product &nbsp;/&nbsp; Category &nbsp;/&nbsp; FAQ's &nbsp;/&nbsp; Contact Us</div>
  <div class="footer-social"><span></span><span></span><span></span><span></span><span></span></div>
  <div class="copyright">© 2016 RIDGEWAY BANNERS. ALL RIGHTS RESERVED.</div>
</footer>

</body>
</html>
```